Need website for LED Signs company

Need an web page for a sign company. Basic home page / Tab for photo gallery (projects), tab for other projects could be photo gallery type with the ability for descriptions gallery to be able to have albums (projects) and tab for about us / testimonials Should be easy for me to change with dreamweaver or easy to change add remove content. I will provide pictures and content I would be happy if it could be set up like a template where i can add the content after but i would provide as much content as possible the current page is http://glowcrestsigns.ca examples of my competition:https://metroled.com/led-message-signs/http://www.libertevision.com/https://www.daktronics.com/en-us/products/message-displaysSEO optimized

1 page

• I want to feature LED signs and EMC's the Special projects tab tab will or should be a photo type gallery that is easy to add photos with detailed descriptions
• I do not want to wast peoples time making something similar to what i have now.
• To help me pick a winner Please show links to some of the sites you have created in the past. .

```html
<!DOCTYPE html>
<html lang="en">
<head>
<meta charset="utf-8">
<title>Glowcrest Signs – The Future of LED Technology</title>
<link href="https://fonts.googleapis.com/css2?family=Oswald:wght@400;500&family=Lato:wght@400;700&display=swap" rel="stylesheet">
<style>
:root{
  --blue:#0d4fc4;
  --blue-dark:#0a3a9c;
  --blue-deep:#072a7a;
  --ink:#1c1c1c;
  --text:#555;
  --muted:#8c8c8c;
  --white:#fff;
  --field:#f1f1f1;
  --line:#dcdcdc;
}
*{box-sizing:border-box;margin:0;padding:0}
html,body{width:1200px;height:3896px;overflow:hidden}
body{position:relative;background:var(--white);font-family:'Lato',Arial,sans-serif;color:var(--text)}
.abs{position:absolute}
h1,h2,h3,.oswald{font-family:'Oswald','Arial Narrow',sans-serif;font-weight:400}

/* header */
.site-header{top:0;left:0;width:1200px;height:169px;background:#f7f7f7}
.brand{left:78px;top:30px;font-family:'Oswald','Arial Narrow',sans-serif;font-size:48px;font-weight:500;color:#9a9a9a;letter-spacing:1px;display:flex;align-items:center;gap:14px}
.brand-mark{width:20px;height:20px;background:var(--blue)}
.call{right:78px;top:40px;display:flex;align-items:center;gap:14px}
.call small{display:block;font-size:15px;color:var(--muted)}
.call strong{display:block;font-size:24px;color:var(--blue-dark);font-weight:700}

/* nav */
.main-nav{left:78px;top:132px;width:1044px;height:71px;background:var(--blue);border-radius:6px;z-index:5;display:flex;align-items:center;padding:0 34px;box-shadow:0 4px 10px rgba(0,0,0,.25)}
.main-nav a{color:var(--white);text-decoration:none;font-size:17px;margin-right:58px}
.main-nav a.current{font-weight:700;border-bottom:2px solid var(--white);padding-bottom:4px}
.search{margin-left:auto;width:210px;height:32px;background:var(--white);border-radius:16px;display:flex;align-items:center;justify-content:space-between;padding:0 4px 0 14px;font-size:13px;color:#777}
.search span.btn{width:32px;height:26px;background:var(--blue);border-radius:13px;display:flex;align-items:center;justify-content:center}

/* hero */
.hero{top:169px;left:0;width:1200px;height:602px;background:linear-gradient(180deg,#3b3a2c 0%,#5a4a35 40%,#2a3440 75%,#1d2a33 100%)}
.hero-title{top:140px;width:1200px;text-align:center;color:var(--white);font-size:72px;line-height:82px;text-shadow:0 2px 8px rgba(0,0,0,.5)}
.hero-title .r{color:#e52b2b}.hero-title .g{color:#2fcf3c}.hero-title .b{color:#2b6bf0}
.hero-text{top:320px;left:270px;width:660px;text-align:center;color:var(--white);font-size:15px;line-height:24px}
.btn-primary{background:var(--blue);color:var(--white);border-radius:24px;font-size:18px;display:flex;align-items:center;justify-content:center;font-family:'Oswald','Arial Narrow',sans-serif;letter-spacing:.5px}
.hero .btn-primary{top:438px;left:517px;width:166px;height:48px}
.slide-arrow{top:290px;width:50px;height:50px;border-radius:50%;display:flex;align-items:center;justify-content:center}
.slide-arrow.prev{left:50px;background:rgba(255,255,255,.85)}
.slide-arrow.next{right:48px;border:2px solid var(--white);background:rgba(0,0,0,.3)}

/* welcome */
.section-title{width:1200px;text-align:center;font-size:42px;color:var(--ink);text-transform:uppercase}
.section-title em{font-style:normal;color:var(--blue)}
.welcome-title{top:822px}
.welcome-text{top:904px;left:250px;width:700px;text-align:center;font-size:14px;line-height:24px}
.scroll-down{top:1026px;left:574px;width:52px;height:52px;border:2px solid #b8c8e8;border-radius:50%;display:flex;align-items:center;justify-content:center}

/* services */
.services{top:1143px;left:0;width:1200px;height:792px;background:linear-gradient(180deg,#1363d6 0%,#0b4cc0 50%,#0a3a9e 100%)}
.services .section-title{top:46px;color:var(--white)}
.services-intro{top:132px;left:280px;width:640px;text-align:center;color:var(--white);font-size:15px;line-height:25px}
.service-card{top:207px;width:499px;height:502px;background:var(--white);box-shadow:0 6px 16px rgba(0,0,0,.3)}
.service-card .photo{position:absolute;left:16px;top:21px;width:467px;height:312px}
.service-card h3{position:absolute;left:16px;top:354px;font-family:'Lato',Arial,sans-serif;font-size:20px;font-weight:400;color:var(--ink)}
.service-card p{position:absolute;left:16px;top:394px;width:440px;font-size:14px;line-height:23px;color:#9a9a9a}
.read-more{position:absolute;left:16px;top:458px;display:flex;align-items:center;gap:10px;font-size:14px;font-weight:700;color:var(--blue)}

/* gallery */
.gallery-title{top:1988px}
.gallery-tile{width:239px;height:205px;background:var(--white);box-shadow:0 2px 10px rgba(0,0,0,.22);padding:14px}
.gallery-tile div{width:100%;height:100%}

/* testimonial */
.testimonials{top:2831px;left:0;width:1200px;height:563px;background:linear-gradient(180deg,#2c3745 0%,#3a3f48 55%,#221c1c 100%)}
.testimonials .section-title{top:50px;color:var(--white)}
.quote-card{top:137px;left:239px;width:725px;height:364px;background:rgba(13,79,196,.92);border-radius:14px;color:var(--white);text-align:center}
.avatar{position:absolute;left:318px;top:50px;width:88px;height:88px;border-radius:50%;background:#d9dee6;border:4px solid var(--white)}
.client-name{position:absolute;top:160px;width:100%;font-size:16px}
.quote{position:absolute;top:198px;left:60px;width:605px;font-size:14px;line-height:24px}
.dots{position:absolute;top:300px;width:100%;display:flex;justify-content:center;gap:8px}
.dots span{width:12px;height:12px;border:1.5px solid var(--white);border-radius:50%}
.dots span.on{background:var(--white)}

/* contact */
.touch-title,.contact-title{top:3452px;font-size:40px;color:var(--ink);text-transform:uppercase}
.touch-title{left:78px}.contact-title{left:475px}
.touch-title em,.contact-title em{font-style:normal;color:var(--blue)}
.info{left:78px;display:flex;gap:16px}
.info .ico{width:24px;display:flex;justify-content:center}
.info b{display:block;font-family:'Oswald','Arial Narrow',sans-serif;font-weight:400;color:var(--blue);font-size:16px;text-transform:uppercase}
.info span{display:block;font-size:13px;color:#444;margin-top:6px}
.follow{left:78px;top:3726px;display:flex;align-items:center;gap:14px;font-size:13px;color:#444}
.follow i{width:40px;height:40px;border-radius:50%;background:var(--blue);display:block}
.field{background:linear-gradient(180deg,#fafafa,#ececec);border:1px solid var(--line);font-size:13px;color:#999;padding:18px 14px 0}
.contact-form .btn-primary{top:3718px;left:475px;width:166px;height:48px;font-size:18px}

/* footer */
.site-footer{top:3831px;left:0;width:1200px;height:65px;background:var(--blue);color:var(--white);font-size:14px;display:flex;align-items:center;justify-content:center}
.site-footer b{margin:0 5px}
</style>
</head>
<body>

<header class="site-header abs">
  <div class="brand abs"><span class="brand-mark"></span>GLOWCREST SIGNS</div>
  <div class="call abs">
    <svg width="34" height="40" viewBox="0 0 24 24"><path fill="#0d4fc4" d="M6.6 10.8c1.4 2.8 3.8 5.1 6.6 6.6l2.2-2.2c.3-.3.7-.4 1-.2 1.1.4 2.3.6 3.6.6.6 0 1 .4 1 1V20c0 .6-.4 1-1 1C10.6 21 3 13.4 3 4c0-.6.4-1 1-1h3.5c.6 0 1 .4 1 1 0 1.3.2 2.5.6 3.6.1.3 0 .7-.2 1z"/></svg>
    <div><small>Call Us Now</small><strong>(306) 555-0148</strong></div>
  </div>
</header>

<nav class="main-nav abs">
  <a class="current">Home</a><a>Services</a><a>About Us</a><a>Gallery</a><a>Downloads</a><a>Technology</a><a>Contact Us</a>
  <div class="search">Search here...
    <span class="btn"><svg width="14" height="14" viewBox="0 0 24 24"><circle cx="10" cy="10" r="6" fill="none" stroke="#fff" stroke-width="3"/><path d="M15 15l6 6" stroke="#fff" stroke-width="3"/></svg></span>
  </div>
</nav>

<section class="hero abs" role="img" aria-label="Evening photo of a resort courtyard with palm trees and a lit pool">
  <h1 class="hero-title abs">The Future of<br><span class="r">L</span><span class="g">.E.</span><span class="b">D</span> technology</h1>
  <p class="hero-text abs">Lorem ipsum dolor sit amet, consectetur adipiscing elit, sed do eiusmod tempor incididunt ut labore et dolore magna aliqua. Ut enim ad minim veniam, quis nostrud exercitation ullamco laboris nisi ut aliquip ex ea commodo consequat.</p>
  <a class="btn-primary abs">CONTACT US</a>
  <div class="slide-arrow prev abs"><svg width="16" height="16" viewBox="0 0 16 16"><path d="M10 3L5 8l5 5" fill="none" stroke="#0d4fc4" stroke-width="2.5"/></svg></div>
  <div class="slide-arrow next abs"><svg width="16" height="16" viewBox="0 0 16 16"><path d="M6 3l5 5-5 5" fill="none" stroke="#fff" stroke-width="2.5"/></svg></div>
</section>

<section class="welcome">
  <h2 class="section-title welcome-title abs">Welcome to <em>Glowcrest Signs</em></h2>
  <p class="welcome-text abs">Glowcrest Signs is not your average L.E.D. Company. Our technology and custom made LED modules have what is takes to make your custom project come to life. Our team will work with you to create your wildest projects. No project is to big or to small. From digital signage, video walls, window signs or custom made DJ booths, Glowcrest Signs will exceed your expectations.</p>
  <div class="scroll-down abs"><svg width="18" height="24" viewBox="0 0 18 24"><path d="M9 2v19M3 15l6 6 6-6" fill="none" stroke="#0d4fc4" stroke-width="2"/></svg></div>
</section>

<section class="services abs">
  <h2 class="section-title abs">Our Services</h2>
  <p class="services-intro abs">We are a custom build service. If you can dream it, we can build it. From outdoor displays in your back yard, to massive video walls for indoor and outdoor applications.</p>
  <article class="service-card abs" style="left:78px">
    <div class="photo" role="img" aria-label="Photo of an indoor lobby with carved statues and warm lighting" style="background:linear-gradient(160deg,#6b4a2e,#a57a4e 50%,#3b2a1c)"></div>
    <h3>Massive video walls for indoor applications</h3>
    <p>Lorem ipsum dolor sit amet, consectetur adipiscing elit, sed do eiusmod tempor incididunt ut labore et dolore magna aliqua.</p>
    <span class="read-more">READ MORE <svg width="36" height="12" viewBox="0 0 36 12"><path d="M0 6h34M28 1l6 5-6 5" fill="none" stroke="#0d4fc4" stroke-width="1.5"/></svg></span>
  </article>
  <article class="service-card abs" style="left:623px">
    <div class="photo" role="img" aria-label="Photo of a busy city square lined with large outdoor LED billboards" style="background:linear-gradient(160deg,#3a4a6a,#7a5a8a 45%,#c94a4a 70%,#2a2a3a)"></div>
    <h3>Massive video walls for outdoor applications</h3>
    <p>Lorem ipsum dolor sit amet, consectetur adipiscing elit, sed do eiusmod tempor incididunt ut labore et dolore magna aliqua.</p>
    <span class="read-more">READ MORE <svg width="36" height="12" viewBox="0 0 36 12"><path d="M0 6h34M28 1l6 5-6 5" fill="none" stroke="#0d4fc4" stroke-width="1.5"/></svg></span>
  </article>
</section>

<section class="gallery">
  <h2 class="section-title gallery-title abs">Our <em>Work Gallery</em></h2>
  <div class="gallery-tile abs" style="left:78px;top:2075px"><div role="img" aria-label="Outdoor sign in a street with trees" style="background:linear-gradient(160deg,#5a6a5a,#8a9a8a)"></div></div>
  <div class="gallery-tile abs" style="left:345px;top:2075px"><div role="img" aria-label="Illuminated storefront sign at night" style="background:linear-gradient(160deg,#1a1410,#5a4a38)"></div></div>
  <div class="gallery-tile abs" style="left:615px;top:2075px"><div role="img" aria-label="Purple lit interior display" style="background:linear-gradient(160deg,#1a1020,#5a2a6a)"></div></div>
  <div class="gallery-tile abs" style="left:883px;top:2075px"><div role="img" aria-label="Blue LED lit aquarium installation" style="background:linear-gradient(160deg,#0a1a4a,#2a5ad0)"></div></div>
  <div class="gallery-tile abs" style="left:78px;top:2314px"><div role="img" aria-label="Glowing LED cube sculpture" style="background:linear-gradient(160deg,#2a0a0a,#d8502a)"></div></div>
  <div class="gallery-tile abs" style="left:345px;top:2314px"><div role="img" aria-label="Vertical digital display kiosk" style="background:linear-gradient(160deg,#1a1a2a,#3a4ab0)"></div></div>
  <div class="gallery-tile abs" style="left:615px;top:2314px"><div role="img" aria-label="LED street light poles at dusk" style="background:linear-gradient(160deg,#1a2a3a,#3a4a5a)"></div></div>
  <div class="gallery-tile abs" style="left:883px;top:2314px"><div role="img" aria-label="Neon open sign in a window" style="background:linear-gradient(160deg,#1a1a3a,#b02a4a)"></div></div>
  <div class="gallery-tile abs" style="left:78px;top:2553px"><div role="img" aria-label="Building facade covered with large billboards" style="background:linear-gradient(160deg,#c82a2a,#5a6ab0)"></div></div>
  <div class="gallery-tile abs" style="left:345px;top:2553px"><div role="img" aria-label="Event stage with LED video wall" style="background:linear-gradient(160deg,#1a2a8a,#c02a4a)"></div></div>
  <div class="gallery-tile abs" style="left:615px;top:2553px"><div role="img" aria-label="LED departure board with scrolling text" style="background:linear-gradient(160deg,#1a1a1a,#4a2a1a)"></div></div>
  <div class="gallery-tile abs" style="left:883px;top:2553px"><div role="img" aria-label="Lit cafe sign on a storefront" style="background:linear-gradient(160deg,#2a1a10,#6a4a30)"></div></div>
</section>

<section class="testimonials abs" role="img" aria-label="Night street scene with lit neon signs">
  <h2 class="section-title abs">Clients Testimonial</h2>
  <div class="quote-card abs">
    <div class="avatar" role="img" aria-label="Client portrait"></div>
    <div class="client-name">- Client Name</div>
    <p class="quote">Lorem ipsum dolor sit amet, consectetur adipiscing elit, sed do eiusmod tempor incididunt ut labore et dolore magna aliqua. Ut enim ad minim veniam, quis nostrud exercitation ullamco laboris nisi ut aliquip ex ea commodo consequat.</p>
    <div class="dots"><span></span><span class="on"></span><span></span></div>
  </div>
</section>

<section class="contact">
  <h2 class="touch-title abs oswald">Get in <em>Touch</em></h2>
  <div class="info abs" style="top:3526px">
    <div class="ico"><svg width="16" height="22" viewBox="0 0 16 22"><path d="M8 0C3.6 0 0 3.4 0 7.8 0 13 8 22 8 22s8-9 8-14.2C16 3.4 12.4 0 8 0zm0 11a3 3 0 110-6 3 3 0 010 6z" fill="#0d4fc4"/></svg></div>
    <div><b>Address</b><span>Riverbend, Saskatchewan S7X 2K4</span></div>
  </div>
  <div class="info abs" style="top:3596px">
    <div class="ico"><svg width="20" height="20" viewBox="0 0 24 24"><path fill="#0d4fc4" d="M6.6 10.8c1.4 2.8 3.8 5.1 6.6 6.6l2.2-2.2c.3-.3.7-.4 1-.2 1.1.4 2.3.6 3.6.6.6 0 1 .4 1 1V20c0 .6-.4 1-1 1C10.6 21 3 13.4 3 4c0-.6.4-1 1-1h3.5c.6 0 1 .4 1 1 0 1.3.2 2.5.6 3.6.1.3 0 .7-.2 1z"/></svg></div>
    <div><b>Phone</b><span>(306) 555-0148</span></div>
  </div>
  <div class="info abs" style="top:3664px">
    <div class="ico"><svg width="20" height="16" viewBox="0 0 20 16"><rect width="20" height="16" rx="2" fill="#0d4fc4"/><path d="M1 2l9 7 9-7" fill="none" stroke="#fff" stroke-width="1.6"/></svg></div>
    <div><b>Email</b><span>sales@glowcrestsigns.ca</span></div>
  </div>
  <div class="follow abs"><i></i>Follow On : Linkface</div>

  <h2 class="contact-title abs oswald">Contact <em>Us</em></h2>
  <form class="contact-form">
    <div class="field abs" style="left:475px;top:3529px;width:208px;height:60px">Name :</div>
    <div class="field abs" style="left:693px;top:3529px;width:208px;height:60px">Phone :</div>
    <div class="field abs" style="left:911px;top:3529px;width:209px;height:60px">Email :</div>
    <div class="field abs" style="left:475px;top:3599px;width:645px;height:100px">Message / Comments :</div>
    <a class="btn-primary abs">SUBMIT NOW</a>
  </form>
</section>

<footer class="site-footer abs">© 2019 <b>GLOWCREST SIGNS.</b> All rights reserved.</footer>

</body>
</html>
```